job report

Designer – Professional Plumbing Job Report Template

Overview

We are seeking a skilled designer to create a professional, easy-to-use Job Report template for a commercial and maintenance plumbing business.
The report will be used for clients, property managers, facilities managers, strata, and retail centres and must clearly communicate findings, works completed, and recommendations in a polished, compliant, and branded format.

The final document must be suitable for PDF delivery, email, and ongoing reuse.

Objectives

Present plumbing works in a clear, professional, and defensible report format

Improve client understanding of findings and recommendations

Provide a repeatable template that can be used across maintenance, reactive, and investigative works

Allow easy insertion of text, tables, and photos

Report Structure (Minimum Inclusions)
1. Cover Page

Company logo and branding

Report title (e.g. Plumbing Job Report / Investigation Report)

Client name

Site address

Job reference / work order number

Date of attendance

Technician / contractor name

2. Client & Site Details

Client / company name

Site address

Contact person

Contact details

Access notes (after-hours, tenant access, etc.)

3. Reason for Attendance

Clear description of why attendance was required

Call-out type (reactive, scheduled maintenance, investigation, emergency, etc.)

Reported issue or scope requested by client

4. Findings / Observations

Detailed findings discovered on site

Condition of pipework, fixtures, drainage, or systems

Any contributing factors identified

Notes on compliance, wear, damage, or risk

(This section should support bullet points and paragraphs.)

5. Works Carried Out

Step-by-step description of works completed

Equipment used (e.g. jetter, CCTV camera, leak detection, flex shaft, etc.)

Repairs, replacements, testing, and verification

Confirmation that systems were tested and operational on completion

6. Photos & Visual Evidence

Clearly labelled photo sections

Before / during / after photos

Space for photo captions and explanations

Logical layout that aligns photos with written findings

7. Recommendations

Clearly separated from works completed

Urgent vs non-urgent recommendations

Preventative maintenance advice

Upgrade or replacement suggestions

Risk-based language where appropriate

8. Limitations & Exclusions

Areas not inspected

Access limitations

Assumptions made during inspection

Items outside scope of works

9. Conclusion

Summary of outcome

Confirmation of current system status

Next steps (if any)

10. Sign-Off

Contractor / technician name

Company name

Date

Optional client acknowledgement section

Design Requirements

Clean, professional layout

Commercial / trade-appropriate styling (not overly creative)

Easy-to-read fonts

Consistent headings and spacing

Logical flow for busy property managers

Editable format (Word / Google Docs / InDesign source file)

Final export-ready PDF version

Bonus (Nice to Have)

Traffic-light system (Green / Amber / Red) for condition reporting

Iconography for findings, repairs, and recommendations

Optional sections for compliance notes (AS/NCC references)

Space for QR codes or job reference numbers

Deliverables

Editable master report template

PDF version

Instructions or notes for ongoing use

```html
<!DOCTYPE html>
<html lang="en">
<head>
<meta charset="utf-8">
<title>Brightflow Plumbing – Job Report Template</title>
<link href="https://fonts.googleapis.com/css2?family=Montserrat:wght@400;500;600;700;800&display=swap" rel="stylesheet">
<style>
  :root{
    --yellow:#F0B333;
    --blue:#2EAEE1;
    --ink:#111418;
    --body:#3a3d42;
    --white:#ffffff;
    --line:#d9dbde;
  }
  *{box-sizing:border-box;margin:0;padding:0}
  html,body{width:1200px;height:530px;overflow:hidden;background:var(--white)}
  body{font-family:"Montserrat",Arial,sans-serif;color:var(--ink);position:relative}

  .page{position:absolute;top:26px;width:370px;height:478px;background:var(--white);overflow:hidden;box-shadow:0 0 0 1px #ececec}
  .page--cover{left:20px}
  .page--client{left:415px}
  .page--reason{left:810px}

  .top-bar{position:absolute;left:0;top:0;width:100%;height:5px;z-index:2}
  .top-bar--yellow{background:var(--yellow)}
  .top-bar--blue{background:var(--blue)}

  .brand{position:absolute;font-weight:800;color:var(--blue);letter-spacing:.02em;line-height:1;white-space:nowrap;z-index:2}
  .brand--large{left:21px;top:34px;font-size:22px;line-height:1.25}
  .brand--large .brand-dot{display:inline-block;width:10px;height:10px;border-radius:50%;background:var(--yellow);margin-left:5px;vertical-align:middle}
  .brand--small{right:14px;top:18px;font-size:8.5px;text-align:right;line-height:1.1}
  .brand--white{color:var(--white)}

  .title{position:absolute;left:20px;font-weight:800;font-size:18px;line-height:1.15;text-transform:uppercase;white-space:nowrap;z-index:2}
  .title--cover{top:117px;font-size:16.5px}
  .title .accent{color:var(--blue)}
  .title .accent-white{color:var(--white)}
  .subtitle{position:absolute;left:20px;font-size:10.5px;font-weight:500;line-height:1.2;width:215px;z-index:2}

  .photo{position:absolute}
  .photo--cover-bg{left:0;top:189px;width:100%;height:289px;background:linear-gradient(160deg,#3bb3e2 0%,#1f93c7 60%,#1a7fae 100%)}
  .photo--cover-person{left:250px;top:103px;width:120px;height:375px;background:linear-gradient(180deg,#2a3242 0%,#1c2433 100%);border-radius:55px 55px 0 0;z-index:3}
  .photo--client-bg{left:0;top:305px;width:100%;height:173px;background:linear-gradient(150deg,#6f8fa3 0%,#4b6a80 100%)}
  .photo--client-person{left:210px;top:110px;width:160px;height:368px;background:linear-gradient(180deg,#3a57b3 0%,#6f7a87 55%,#838a93 100%);border-radius:60px 60px 0 0}
  .photo--reason{left:0;top:0;width:100%;height:189px;background:linear-gradient(120deg,#e2a93a 0%,#d8a136 55%,#c58f2b 100%)}

  .form-card{position:absolute;background:var(--yellow);border-radius:7px;color:var(--white);z-index:2}
  .form-card--cover{left:19px;top:241px;width:212px;height:182px}
  .form-card--client{left:19px;top:118px;width:186px;height:324px}
  .field-label{position:absolute;left:14px;font-size:7.3px;font-weight:700;letter-spacing:.02em;text-transform:uppercase}
  .field-input{position:absolute;left:14px;height:14px;border:1px solid var(--white);font-size:6px;padding-left:7px;line-height:12px}
  .form-card--cover .field-input{width:172px}
  .form-card--client .field-input{width:158px}
  .notes-box{position:absolute;left:14px;top:188px;width:158px;height:121px;border:1px solid var(--white);padding:11px 9px;font-size:5.6px;line-height:9.7px}
  .notes-box p+p{margin-top:5px}

  .footer{position:absolute;right:0;bottom:0;width:218px;height:20px;background:var(--blue);clip-path:polygon(8px 0,100% 0,100% 100%,0 100%);display:flex;align-items:center;justify-content:flex-end;gap:12px;padding-right:15px;color:var(--white);font-size:6.3px;z-index:4}
  .footer-item{display:flex;align-items:center;gap:5px}
  .footer-item svg{width:8px;height:8px;fill:none;stroke:var(--white);stroke-width:1.6}

  .section-label{position:absolute;left:20px;font-size:7.5px;font-weight:700;color:var(--blue);text-transform:uppercase;letter-spacing:.02em}
  .option{position:absolute;display:flex;align-items:center;gap:4px;font-size:7.2px;color:var(--body)}
  .checkbox{width:8.5px;height:8.5px;border:1px solid #555;border-radius:1px;background:var(--white)}
  .reason-text{position:absolute;left:20px;top:277px;width:312px;font-size:6.9px;line-height:11.2px;color:var(--body);text-align:justify}
  .issue-box{position:absolute;left:20px;top:360px;width:331px;height:85px;border:1px solid var(--line);display:grid;grid-template-columns:1fr 1fr;column-gap:16px;padding:9px 8px 0 10px}
  .issue-list{list-style:none;font-size:6.9px;line-height:11px;color:var(--body)}
  .issue-list li{position:relative;padding-left:10px;margin-bottom:7px}
  .issue-list li::before{content:"";position:absolute;left:0;top:3.5px;width:4px;height:4px;border-radius:50%;background:var(--yellow)}
</style>
</head>
<body>

<section class="page page--cover">
  <div class="top-bar top-bar--yellow"></div>
  <div class="brand brand--large">BRIGHTFLOW<span class="brand-dot"></span><br>PLUMBING</div>
  <h1 class="title title--cover">Plumbing <span class="accent">Job Report</span></h1>
  <p class="subtitle" style="top:141px">Scheduled Maintenance Works &amp; System Condition Summary</p>
  <div class="photo photo--cover-bg" role="img" aria-label="Blue-tinted photo of plumbers at work in a commercial space"></div>
  <div class="photo photo--cover-person" role="img" aria-label="Photo of the lead plumber in a branded navy polo shirt"></div>
  <div class="form-card form-card--cover">
    <span class="field-label" style="top:14px">Client:</span>
    <div class="field-input" style="top:25px"></div>
    <span class="field-label" style="top:46px">Site Address :</span>
    <div class="field-input" style="top:57px"></div>
    <span class="field-label" style="top:78px">Job Reference :</span>
    <div class="field-input" style="top:89px"></div>
    <span class="field-label" style="top:111px">Date of Attendance :</span>
    <div class="field-input" style="top:122px"></div>
    <span class="field-label" style="top:144px">Contractor :</span>
    <div class="field-input" style="top:155px"></div>
  </div>
  <footer class="footer">
    <span class="footer-item"><svg viewBox="0 0 16 16"><path d="M3 1.5l3 3-1.6 2a9 9 0 0 0 5.1 5.1l2-1.6 3 3-2 2A13 13 0 0 1 1 3.5z"/></svg>0400 118 275</span>
    <span class="footer-item"><svg viewBox="0 0 16 16"><rect x="1" y="3" width="14" height="10"/><path d="M1 3l7 6 7-6"/></svg>jordan@brightflowplumbing.com.au</span>
  </footer>
</section>

<section class="page page--client">
  <div class="top-bar top-bar--blue"></div>
  <div class="brand brand--small">BRIGHTFLOW<br>PLUMBING</div>
  <h2 class="title" style="top:32px">Client Information<br><span class="accent">&amp; Site Details</span></h2>
  <p class="subtitle" style="top:77px">Scheduled Maintenance Works &amp; System Condition Summary</p>
  <div class="photo photo--client-bg" role="img" aria-label="Photo of a site office with paperwork on a desk"></div>
  <div class="photo photo--client-person" role="img" aria-label="Photo of a plumber in cap and overalls writing on a clipboard"></div>
  <div class="form-card form-card--client">
    <span class="field-label" style="top:13px">Company Name :</span>
    <div class="field-input" style="top:24px"></div>
    <span class="field-label" style="top:46px">Site Address :</span>
    <div class="field-input" style="top:57px"></div>
    <span class="field-label" style="top:81px">Contact Person :</span>
    <div class="field-input" style="top:92px"></div>
    <span class="field-label" style="top:116px">Contact Details:</span>
    <div class="field-input" style="top:128px">Phone</div>
    <div class="field-input" style="top:148px">Email</div>
    <span class="field-label" style="top:175px">Access Notes :</span>
    <div class="notes-box">
      <p>After-hours access was provided via building security. Works were undertaken with tenant coordination and did not impact occupied areas. No access restrictions were encountered during attendance.</p>
      <p>After-hours access was provided via building security. Works were undertaken with tenant coordination and did not impact occupied areas.</p>
    </div>
  </div>
  <footer class="footer">
    <span class="footer-item"><svg viewBox="0 0 16 16"><path d="M3 1.5l3 3-1.6 2a9 9 0 0 0 5.1 5.1l2-1.6 3 3-2 2A13 13 0 0 1 1 3.5z"/></svg>0400 118 275</span>
    <span class="footer-item"><svg viewBox="0 0 16 16"><rect x="1" y="3" width="14" height="10"/><path d="M1 3l7 6 7-6"/></svg>jordan@brightflowplumbing.com.au</span>
  </footer>
</section>

<section class="page page--reason">
  <div class="photo photo--reason" role="img" aria-label="Yellow-tinted photo of a smiling plumber holding a clipboard in a kitchen"></div>
  <div class="brand brand--small brand--white">BRIGHTFLOW<br>PLUMBING</div>
  <h2 class="title" style="top:32px">Reason<br><span class="accent-white">For Attendance</span></h2>
  <p class="subtitle" style="top:77px;color:var(--white)">Reason for attendance and reported plumbing issues.</p>

  <span class="section-label" style="top:209px">Service Type :</span>
  <span class="option" style="left:20px;top:224px"><span class="checkbox"></span>Reactive Maintenance</span>
  <span class="option" style="left:118px;top:224px"><span class="checkbox"></span>Scheduled Maintenance</span>
  <span class="option" style="left:224px;top:224px"><span class="checkbox"></span>Investigation</span>
  <span class="option" style="left:20px;top:240px"><span class="checkbox"></span>Emergency</span>
  <span class="option" style="left:118px;top:240px"><span class="checkbox"></span>Other</span>

  <span class="section-label" style="top:262px">Reason for Attendance :</span>
  <p class="reason-text">Attendance was requested to assess and address a reported plumbing issue within the tenancy. The client advised of ongoing concerns requiring investigation to determine the cause, confirm the extent of the issue, and carry out appropriate rectification where possible. The assessment was undertaken to minimise operational disruption and reduce the risk of further damage to the property.</p>

  <span class="section-label" style="top:345px">Reported Issue :</span>
  <div class="issue-box">
    <ul class="issue-list">
      <li>Reports of intermittent water leakage observed within the tenancy</li>
      <li>Inspection of visible pipework and fixtures to identify the source of the issue</li>
    </ul>
    <ul class="issue-list">
      <li>Carry out necessary minor rectification works where possible</li>
      <li>Provide recommendations for any further remedial works required</li>
    </ul>
  </div>
  <footer class="footer">
    <span class="footer-item"><svg viewBox="0 0 16 16"><path d="M3 1.5l3 3-1.6 2a9 9 0 0 0 5.1 5.1l2-1.6 3 3-2 2A13 13 0 0 1 1 3.5z"/></svg>0400 118 275</span>
    <span class="footer-item"><svg viewBox="0 0 16 16"><rect x="1" y="3" width="14" height="10"/><path d="M1 3l7 6 7-6"/></svg>jordan@brightflowplumbing.com.au</span>
  </footer>
</section>

</body>
</html>
```